diesel mechanic business card design

granite diesel is a new and upcoming business we are looking for some bad ass designs to help get us started we offer 24 hour road service, off road recovery, welding and custom fabrications we are diesel mechanics so our design should be bold and eye catching flames wrenches engine parts are cool we work in an industrial environment around heavy trucks and equipment this in not a quick grease we fix it all nothing is to big or to small the colors red and black are always a plus but we are open to anything you guys can come up with ready set go

Target Market(s)

other small business primarily trucking and transportation companys

Industry/Entity Type

Business

Contact Information for Business Card

company name Granitte diesel truck & trailer repair / address 14 rear north halloway ave ridgeford ST 00417 / ownersAdam DeLuccie 555-555-0143 / Walter Dombrosky 555-555-0178 E mail brentkovalsky@mailbox-example.com fax 555-555-0192

Requirements
Nice to have
• industrial modern design
Should not have
• rainbows butterfly's unicorns or cupcakes

```html
<!DOCTYPE html>
<html lang="en">
<head>
<meta charset="utf-8">
<title>Granitte diesel truck &amp; trailer repair – business card</title>
<link rel="stylesheet" href="https://fonts.googleapis.com/css2?family=Playfair+Display:wght@500&family=Tinos&display=swap">
<style>
  :root {
    --bg: #e9e7e3;
    --paper-light: #fbfbfb;
    --paper-shade: #dcdcdc;
    --ink: #2b2b2b;
    --black: #0b0b0b;
    --black-soft: #2a2a2a;
    --white: #f4f4f4;
    --truck-red: #d61f26;
    --truck-dark: #3a0c0e;
  }
  * { box-sizing: border-box; margin: 0; padding: 0; }
  html, body { width: 1200px; height: 902px; overflow: hidden; }
  body {
    background: var(--bg);
    display: flex;
    flex-direction: column;
    align-items: center;
    justify-content: center;
    gap: 40px;
  }
  .card {
    position: relative;
    width: 700px;
    height: 400px;
    border-radius: 22px;
    overflow: hidden;
    box-shadow: 0 8px 22px rgba(0,0,0,.22);
    background: linear-gradient(180deg, var(--paper-light), var(--paper-shade));
  }
  .company-name {
    font-family: "Playfair Display", serif;
    font-weight: 500;
    color: var(--ink);
    font-size: 38px;
    line-height: 1.02;
    letter-spacing: -0.5px;
    text-align: center;
    position: absolute;
    left: 0; right: 0;
  }
  /* front */
  .card--front .company-name { top: 58px; }
  .card--front .base-band {
    position: absolute; left: 0; right: 0; top: 190px; bottom: 0;
    background: linear-gradient(180deg, var(--black-soft), var(--black));
  }
  .card--front .photo {
    position: absolute; left: 120px; right: 0; top: 168px; bottom: 0;
    background: linear-gradient(100deg, #b9b9b9 0%, var(--truck-red) 22%, var(--truck-red) 58%, #8d8d8d 70%, var(--truck-dark) 100%);
  }
  /* back */
  .card--back .company-name { top: 92px; }
  .card--back .info-band {
    position: absolute; left: 0; right: 0; top: 205px; bottom: 0;
    background: linear-gradient(180deg, var(--black), var(--black-soft) 70%, var(--black));
    display: flex;
    align-items: center;
    padding: 0 40px;
    font-family: "Tinos", serif;
    color: var(--white);
  }
  .owners {
    width: 300px;
    flex: none;
    text-align: right;
    padding-right: 26px;
    border-right: 1px solid var(--white);
  }
  .owner + .owner { margin-top: 16px; }
  .owner-name { font-size: 24px; line-height: 1.05; }
  .owner-role { font-size: 13px; line-height: 1; }
  .owner-phone { font-size: 16px; }
  .contacts { list-style: none; padding-left: 24px; font-size: 16px; line-height: 1.3; min-width: 0; }
  .contacts li { display: flex; align-items: flex-start; gap: 8px; }
  .contacts span { white-space: nowrap; }
  .contacts svg { width: 14px; height: 14px; margin-top: 3px; flex: none; fill: var(--white); }
</style>
</head>
<body>
  <section class="card card--front">
    <div class="base-band"></div>
    <div class="photo" role="img" aria-label="Photo of a mechanic working on the engine of a red semi truck"></div>
    <h1 class="company-name">Granitte diesel truck<br>&amp; trailer repair</h1>
  </section>

  <section class="card card--back">
    <h1 class="company-name">Granitte diesel truck<br>&amp; trailer repair</h1>
    <div class="info-band">
      <div class="owners">
        <div class="owner">
          <div class="owner-name">Brent Kovalsky</div>
          <div class="owner-role">owner</div>
          <div class="owner-phone">555-555-0143</div>
        </div>
        <div class="owner">
          <div class="owner-name">Walter Dombrosky</div>
          <div class="owner-role">owner</div>
          <div class="owner-phone">555-555-0178</div>
        </div>
      </div>
      <ul class="contacts">
        <li>
          <svg viewBox="0 0 16 16" aria-hidden="true"><rect x="4" y="1" width="8" height="5"/><rect x="1" y="6" width="14" height="6" rx="1"/><rect x="4" y="10" width="8" height="5"/></svg>
          <span>555-555-0192</span>
        </li>
        <li>
          <svg viewBox="0 0 16 16" aria-hidden="true"><path d="M1 3h14v10H1z M1 3l7 6 7-6" stroke="#0b0b0b" stroke-width="1.2"/></svg>
          <span>brentkovalsky@mailbox-example.com</span>
        </li>
        <li>
          <svg viewBox="0 0 16 16" aria-hidden="true"><path d="M8 1a5 5 0 0 0-5 5c0 4 5 9 5 9s5-5 5-9a5 5 0 0 0-5-5zm0 7a2 2 0 1 1 0-4 2 2 0 0 1 0 4z"/></svg>
          <span>14 rear north halloway ave<br>ridgeford ST 00417</span>
        </li>
      </ul>
    </div>
  </section>
</body>
</html>
```